Business card design

I am open to ideas. I was thinking of a vertical design, turning the name 90 degrees and placing it on the left edge, then some clipped portion of the fabulous tree with contact info on the bottom -- special emphasis on Web address:WhimBeads.comFor All Your Beading Needs121 E. Cotati AveCotati, CA 94931(707) 664-8343

```html
<!DOCTYPE html>
<html lang="en">
<head>
<meta charset="utf-8">
<title>Fern Glass Co. — Business Card</title>
<link rel="stylesheet" href="https://fonts.googleapis.com/css2?family=Roboto:wght@300;400;700&family=Oswald:wght@600&display=swap">
<style>
  :root {
    --page: #e9e7e3;
    --ink: #111111;
    --paper: #ffffff;
    --card-black: #0a0a0a;
    --violet: #6b3fa0;
    --green: #7cc242;
    --red: #e8262a;
    --grey-text: #222222;
    --icon: #333333;
  }
  * { box-sizing: border-box; margin: 0; padding: 0; }
  html, body {
    width: 1200px; height: 900px; overflow: hidden;
    background: var(--page);
  }
  .canvas {
    position: relative; width: 1200px; height: 900px;
  }
  .card {
    position: absolute; width: 600px; height: 343px;
    left: 300px; border-radius: 4px; overflow: hidden;
    box-shadow: 0 6px 18px rgba(0,0,0,.18);
  }
  /* Front */
  .card-front { top: 80px; background: var(--card-black); color: var(--paper); }
  .front-brand {
    position: absolute; left: 0; right: 0; top: 128px; text-align: center;
  }
  .brand-name {
    font-family: "Roboto", sans-serif; font-weight: 300;
    font-size: 40px; letter-spacing: 1px; color: var(--paper);
  }
  .brand-tagline {
    margin-top: 18px;
    font-family: "Roboto", sans-serif; font-weight: 400;
    font-size: 13px; letter-spacing: 1.6px; text-transform: uppercase;
    color: var(--paper);
  }
  /* Back */
  .card-back { top: 470px; background: var(--paper); }
  .back-swoosh { position: absolute; inset: 0; }
  .tree-art {
    position: absolute; left: 330px; top: 28px; width: 230px; height: 160px;
    border-radius: 50% 50% 46% 46%;
    background: radial-gradient(ellipse at center,
      rgba(124,194,66,.55) 0%, rgba(246,196,40,.35) 45%, rgba(107,63,160,.18) 75%, rgba(255,255,255,0) 100%);
  }
  .contact {
    position: absolute; left: 70px; top: 78px; width: 200px;
    font-family: "Roboto", sans-serif; color: var(--grey-text);
    text-align: center;
  }
  .contact-icon { display: block; margin: 0 auto 6px; }
  .contact-phone { font-weight: 700; font-size: 22px; letter-spacing: .3px; margin-bottom: 12px; }
  .contact-address { font-weight: 400; font-size: 17px; line-height: 1.3; }
  .web {
    position: absolute; right: 22px; top: 232px;
    font-family: "Oswald", sans-serif; font-weight: 600; font-size: 24px;
    letter-spacing: .2px;
  }
  .web-prefix { color: var(--violet); }
  .web-name { color: var(--green); }
  .web-suffix { color: var(--red); }
</style>
</head>
<body>
<main class="canvas">

  <section class="card card-front" aria-label="Card front">
    <div class="front-brand">
      <div class="brand-name">Fern Glass Co.</div>
      <div class="brand-tagline">For all your beading needs</div>
    </div>
  </section>

  <section class="card card-back" aria-label="Card back">
    <svg class="back-swoosh" viewBox="0 0 600 343" width="600" height="343" aria-hidden="true">
      <defs>
        <linearGradient id="swoosh-edge" x1="0" x2="1" y1="0" y2="0">
          <stop offset="0" stop-color="#a6d36b"/>
          <stop offset=".35" stop-color="#8a63c2"/>
          <stop offset="1" stop-color="#5b2f91"/>
        </linearGradient>
      </defs>
      <path d="M0,316 C150,318 250,292 320,244 C410,184 510,166 600,160 L600,172 C515,178 420,196 332,254 C260,302 160,328 0,330 Z" fill="url(#swoosh-edge)"/>
      <path d="M0,330 C160,328 260,302 332,254 C420,196 515,178 600,172 L600,343 L0,343 Z" fill="#0a0a0a"/>
    </svg>

    <div class="tree-art" role="img" aria-label="Rainbow tree illustration with a swing"></div>

    <div class="contact">
      <svg class="contact-icon" width="30" height="30" viewBox="0 0 30 30" aria-hidden="true">
        <circle cx="15" cy="15" r="13" fill="none" stroke="var(--icon)" stroke-width="2.4"/>
        <path d="M11 9 L13.2 9 L14 12 L12.6 13.2 C13.3 14.8 14.6 16.1 16.2 16.8 L17.4 15.4 L20.4 16.2 L20.4 18.4 C20.4 19.2 19.7 19.8 18.9 19.7 C14 19.2 10.2 15.4 9.7 10.5 C9.6 9.7 10.2 9 11 9 Z" fill="var(--icon)"/>
      </svg>
      <div class="contact-phone">(707) 555-0192</div>
      <svg class="contact-icon" width="30" height="30" viewBox="0 0 30 30" aria-hidden="true">
        <circle cx="15" cy="15" r="13" fill="none" stroke="var(--icon)" stroke-width="2.4"/>
        <path d="M15 7.5 C11.8 7.5 9.6 9.8 9.6 12.8 C9.6 16.6 15 22.5 15 22.5 C15 22.5 20.4 16.6 20.4 12.8 C20.4 9.8 18.2 7.5 15 7.5 Z" fill="var(--icon)"/>
        <circle cx="15" cy="12.8" r="2.1" fill="var(--paper)"/>
      </svg>
      <div class="contact-address">348 W. Brindle Ave<br>Larkdale, CA 95410</div>
    </div>

    <div class="web"><span class="web-prefix">www.</span><span class="web-name">FernGlassco</span><span class="web-suffix">.com</span></div>
  </section>

</main>
</body>
</html>
```